Marwick Family Chiropractic Stationary

The letterhead and business card must have our logo.
We would like to see the logo used in different ways ( It can be expanded upon in the stationary.)
Please use the the same or similar colors.
Must be eye catching and memorable.
Must be easy to read

Reason: The doctor has been too busy to make any final decisions. He would like to give himself a little more time.

Target Market(s)

Chiropractic Healthcare

Industry/Entity Type

Business

Requirements
Must have
• Dr. Leonard Marwick D.C.
Chiropractor

555-555-0183

417 Birchfield Road, 2nd Floor
Wrenmoor, WM 06091

drmarwick@marwickspine.example
www.marwickspine.example
www.facebook.com/MarwickFamilySpine
Should not have
• should not be difficult to read

```html
<!DOCTYPE html>
<html lang="en">
<head>
<meta charset="utf-8">
<title>Marwick Family Chiropractic – Business Card</title>
<link rel="stylesheet" href="https://fonts.googleapis.com/css2?family=Questrial&display=swap">
<style>
  :root {
    --backdrop: #3a3a3a;
    --card-dark: #1c1c1c;
    --card-light: #fafafa;
    --brand-green: #2f9e3a;
    --leaf-lime: #b7cf2a;
    --text-grey: #6d6d6d;
    --rule-grey: #9a9a9a;
    --text-light: #e6e6e6;
  }
  * { margin: 0; padding: 0; box-sizing: border-box; }
  html, body { width: 1200px; height: 900px; overflow: hidden; }
  body {
    background: var(--backdrop);
    font-family: "Questrial", "Century Gothic", sans-serif;
    position: relative;
  }
  .card {
    position: absolute;
    left: 280px;
    width: 640px;
    height: 352px;
    border-radius: 2px;
    box-shadow: 0 10px 30px rgba(0,0,0,.45);
  }
  /* Back of card */
  .card-back {
    top: 62px;
    background: var(--card-dark);
  }
  .card-back .wordmark {
    position: absolute;
    left: 0; right: 0; top: 118px;
    display: flex; align-items: center; justify-content: center; gap: 14px;
    color: var(--brand-green);
    font-size: 30px;
    letter-spacing: 1px;
  }
  .wordmark-dot {
    width: 30px; height: 30px; border-radius: 50%;
    background: var(--leaf-lime);
  }
  .card-back .website {
    position: absolute;
    left: 0; right: 0; top: 250px;
    text-align: center;
    color: var(--text-light);
    font-size: 17px;
    letter-spacing: .5px;
  }
  /* Front of card */
  .card-front {
    top: 486px;
    background: var(--card-light);
  }
  .card-front .mark {
    position: absolute; left: 52px; top: 40px;
    width: 64px; height: 64px; border-radius: 50%;
    background: var(--leaf-lime);
  }
  .doctor {
    position: absolute; right: 44px; top: 110px;
    text-align: right;
  }
  .doctor-name {
    color: var(--brand-green);
    font-size: 22px;
    letter-spacing: .5px;
  }
  .doctor-title {
    color: var(--text-grey);
    font-size: 12px;
    margin-top: 2px;
  }
  .rule {
    position: absolute; height: 1px; background: var(--rule-grey);
  }
  .rule-doctor { right: 44px; top: 158px; width: 300px; }
  .rule-base { left: 40px; top: 250px; width: 560px; }
  .contact {
    position: absolute; right: 44px; top: 172px;
    color: var(--text-grey);
    font-size: 14px;
    line-height: 24px;
    text-align: right;
  }
  .contact-line { display: flex; align-items: center; justify-content: flex-end; gap: 6px; white-space: nowrap; }
  .contact-line svg { width: 13px; height: 13px; fill: var(--leaf-lime); flex: none; }
  .card-front .wordmark {
    position: absolute; left: 40px; top: 264px;
    color: var(--brand-green);
    line-height: 1.05;
  }
  .wordmark-name { font-size: 36px; letter-spacing: 1px; }
  .wordmark-sub { font-size: 12px; letter-spacing: 1.5px; }
</style>
</head>
<body>
  <section class="card card-back" aria-label="Business card back">
    <div class="wordmark">
      <span class="wordmark-dot"></span>
      <span>Marwick Family Chiropractic</span>
    </div>
    <p class="website">www.marwickspine.example</p>
  </section>

  <section class="card card-front" aria-label="Business card front">
    <span class="mark"></span>

    <div class="doctor">
      <p class="doctor-name">Dr. Leonard Marwick D.C.</p>
      <p class="doctor-title">Chiropractor</p>
    </div>
    <span class="rule rule-doctor"></span>

    <div class="contact">
      <p class="contact-line">
        <svg viewBox="0 0 24 24" aria-hidden="true"><path d="M12 2a7 7 0 0 0-7 7c0 5 7 13 7 13s7-8 7-13a7 7 0 0 0-7-7zm0 9.5A2.5 2.5 0 1 1 12 6.5a2.5 2.5 0 0 1 0 5z"/></svg>
        417 Birchfield Road, 2nd Floor Wrenmoor, WM 06091
      </p>
      <p class="contact-line">
        <svg viewBox="0 0 24 24" aria-hidden="true"><path d="M6.6 10.8a15 15 0 0 0 6.6 6.6l2.2-2.2a1 1 0 0 1 1-.25 11.4 11.4 0 0 0 3.6.57 1 1 0 0 1 1 1V20a1 1 0 0 1-1 1A17 17 0 0 1 3 4a1 1 0 0 1 1-1h3.5a1 1 0 0 1 1 1c0 1.25.2 2.45.57 3.57a1 1 0 0 1-.25 1z"/></svg>
        555-555-0183
        <svg viewBox="0 0 24 24" aria-hidden="true"><path d="M3 5h18v14H3zm2 2v.5l7 4.5 7-4.5V7zm0 2.9V17h14V9.9l-7 4.5z"/></svg>
        drmarwick@marwickspine.example
      </p>
    </div>

    <span class="rule rule-base"></span>

    <div class="wordmark">
      <p class="wordmark-name">MARWICK</p>
      <p class="wordmark-sub">FAMILY CHIROPRACTIC</p>
    </div>
  </section>
</body>
</html>
```